Modern Medical Optometry Website

We need mordern, Patient friendly website. Easy to navigate and enhance our advance medical technology and excellent patient care.
1. HOME PAGE
2. OUR TEAM PAGE
3. EYECARE PAGE - VISION SERVICES, EYE EXAMS, KERATOCONUS CENTER, GLAUCOMA , DIABITES, MELORIDEX EXAM, DIGITAL RETINAL, OCT.
4. MYOPIA CONTROL CLINIC
5. DRY EYE CLINIC
6. EYEWEAR
7. PATIENT CENTER - BLOG
7. CONTACT US
This is our current website www.brivaloka.com
and We want to add more content and a cleaner design like these website
http://tarnwickfolvendale.com/
https://www.qmvorlu.com/

```html
<!DOCTYPE html>
<html lang="en">
<head>
<meta charset="utf-8">
<title>Lumivue Optometry – Eye Glass Lenses</title>
<link rel="stylesheet" href="https://fonts.googleapis.com/css2?family=Raleway:wght@400;600;700&family=Mulish:wght@400;700&display=swap">
<style>
:root{
  --teal:#0b8db1;
  --yellow:#fbdd2d;
  --footer:#f8e25c;
  --band:#efefef;
  --ink:#2a2a2a;
  --muted:#8a8a8a;
  --nav:#7d7d7d;
  --dark:#2b2b2b;
}
*{box-sizing:border-box;margin:0;padding:0}
html,body{width:691px;height:1200px;overflow:hidden;background:#fff}
body{position:relative;font-family:"Mulish",sans-serif;color:var(--ink)}
.abs{position:absolute}
.topbar{left:0;top:0;width:691px;height:30px;background:var(--teal)}
.topbar-item{top:0;height:30px;display:flex;align-items:center;gap:7px;color:#fff;font-size:8.5px;border-left:1px solid rgba(255,255,255,.25);padding:0 11px}
.social-cell{top:0;width:30px;height:30px;border-left:1px solid rgba(255,255,255,.25);display:flex;align-items:center;justify-content:center}
.social-cell span{width:6px;height:6px;border-radius:50%;background:var(--yellow)}
.brand-box{left:44px;top:12px;width:64px;height:82px;background:#fff;display:flex;flex-direction:column;align-items:center;justify-content:center;gap:5px}
.brand-box .mark{width:26px;height:26px;background:var(--yellow)}
.brand-box .name{font-family:"Raleway",sans-serif;font-size:7.5px;color:#555;text-align:center;line-height:1.15;font-weight:400}
.nav{top:63px;left:127px;display:flex;gap:0;font-family:"Raleway",sans-serif;font-size:9.6px;color:var(--nav)}
.nav a{text-decoration:none;color:inherit;margin-right:21px;letter-spacing:.2px}
.nav a.active{color:var(--teal)}
.search{left:635px;top:63px}
.title-band{left:0;top:108px;width:691px;height:78px;background:var(--band);display:flex;align-items:center;justify-content:center}
.title-band h1{font-family:"Raleway",sans-serif;font-weight:700;font-size:21px;color:var(--teal)}
.photo{left:44px;top:217px;width:291px;height:240px;background:linear-gradient(135deg,#e9c9a6,#b98a66 45%,#6c5a52)}
.intro{left:361px;top:248px;width:265px}
.intro h2{font-family:"Raleway",sans-serif;font-weight:700;font-size:13px;line-height:21px;color:var(--teal)}
.intro .lead{margin-top:10px;font-size:8.3px;font-weight:700;line-height:15px}
.intro .body{margin-top:15px;font-size:8.3px;line-height:15px;color:#555}
.steps-head{left:46px;top:500px;width:600px}
.steps-head h2{font-family:"Raleway",sans-serif;font-weight:700;font-size:18px;color:var(--teal)}
.steps-head p{margin-top:8px;font-size:8.3px;line-height:15px;color:var(--muted)}
.step{top:573px;width:180px}
.step .icon{width:48px;height:48px;border-radius:50%;background:var(--teal);display:flex;align-items:center;justify-content:center}
.step h3{margin-top:10px;font-family:"Raleway",sans-serif;font-weight:700;font-size:12.5px;color:var(--ink)}
.step p{margin-top:6px;font-size:8.3px;line-height:15px;color:var(--muted)}
.step .btn{margin-top:8px;width:102px;height:30px;background:var(--yellow);display:flex;align-items:center;justify-content:center;font-family:"Raleway",sans-serif;font-size:10px;color:var(--ink)}
.labels{top:795px;left:46px;width:600px;display:flex}
.labels div{width:102px;text-align:center;font-family:"Raleway",sans-serif;font-weight:700;font-size:11.5px;color:#111;letter-spacing:.5px}
.frames{top:846px;left:56px;display:flex;gap:35px}
.frames div{width:67px;height:30px;border-radius:14px;background:linear-gradient(90deg,#d9d9d9,#f1f1f1)}
.footer{left:0;top:924px;width:691px;height:234px;background:var(--footer)}
.col{top:957px;width:200px}
.col h4{font-family:"Raleway",sans-serif;font-weight:700;font-size:12px;color:var(--teal);margin-bottom:12px}
.row{display:flex;gap:11px;font-size:8.3px;line-height:15px;color:#333;margin-bottom:9px}
.row svg{flex:none;margin-top:1px}
.hours p{font-size:8.3px;line-height:12px;margin-bottom:6px;color:#333}
.pill{top:1104px;width:161px;height:24px;border-radius:12px;background:var(--dark);color:#fff;font-size:8.3px;display:flex;align-items:center;padding-left:10px;gap:12px}
.dot{top:1104px;width:24px;height:24px;border-radius:50%;background:var(--dark)}
.copyright{left:0;top:1158px;width:691px;height:42px;border-top:1px solid #f3ee9c;background:var(--footer);display:flex;align-items:center;justify-content:center;font-size:8px;color:#555}
.copyright b{color:var(--teal);margin:0 3px}
</style>
</head>
<body>

<div class="abs topbar"></div>
<div class="abs topbar-item" style="left:267px">
  <svg width="11" height="11" viewBox="0 0 24 24" fill="none" stroke="#fff" stroke-width="2"><path d="M5 3h4l2 5-3 2a12 12 0 0 0 6 6l2-3 5 2v4a2 2 0 0 1-2 2A18 18 0 0 1 3 5a2 2 0 0 1 2-2z"/></svg>555-210-4410</div>
<div class="abs topbar-item" style="left:365px">
  <svg width="12" height="10" viewBox="0 0 24 18" fill="none" stroke="#fff" stroke-width="2"><rect x="1" y="1" width="22" height="16"/><path d="M1 1l11 9 11-9"/></svg>hello@lumivueoptics.com</div>
<div class="abs social-cell" style="left:527px"><span></span></div>
<div class="abs social-cell" style="left:557px"><span></span></div>
<div class="abs social-cell" style="left:587px"><span></span></div>
<div class="abs social-cell" style="left:617px;border-right:1px solid rgba(255,255,255,.25)"><span></span></div>

<div class="abs brand-box"><div class="mark"></div><div class="name">LUMIVUE<br>OPTOMETRY</div></div>

<nav class="abs nav">
  <a href="#">HOME</a><a href="#">OUR TEAM</a><a href="#" class="active">EYE CARE</a><a href="#">MYOPIA CONTROL CLINIC</a><a href="#">EYEWEAR</a><a href="#">BLOG</a><a href="#">CONTACT US</a>
</nav>
<svg class="abs search" width="12" height="12" viewBox="0 0 24 24" fill="none" stroke="#0b8db1" stroke-width="2"><circle cx="10" cy="10" r="7"/><path d="M15 15l7 7"/></svg>

<div class="abs title-band"><h1>EYE GLASS LENSES</h1></div>

<div class="abs photo" role="img" aria-label="Photo of a smiling couple taking a selfie, the man wearing glasses"></div>
<div class="abs intro">
  <h2>LOREM IPSUM IS SIMPLY DUMMY TEXT AND PRINTIGN TYPESETTING.</h2>
  <p class="lead">Lorem Ipsum is simply dummy text of the printing and typesetting industry. Lorem Ipsum has been the industry's standard dummy text ever since the 1500.</p>
  <p class="body">when an unknown printer took a galley of type and scrambled it to make a type specimen book. It has survived not only five centuries, but also the leap into electronic typesetting, remaining essentially unchanged.</p>
</div>

<div class="abs steps-head">
  <h2>CHOOSING A LENS IS AS EASY AS 1, 2, 3.</h2>
  <p>Lorem Ipsum is simply dummy text of the printing and typesetting industry. Lorem Ipsum has been the industry's standard dummy text ever since the 1500.when an unknown printer took a galley.</p>
</div>

<div class="abs step" style="left:44px">
  <div class="icon"><svg width="24" height="24" viewBox="0 0 24 24" fill="none" stroke="#fff" stroke-width="1.5"><ellipse cx="12" cy="12" rx="9" ry="7" transform="rotate(40 12 12)"/><path d="M8 8l6 8"/></svg></div>
  <h3>1. LENS TYPES</h3>
  <p>Lorem Ipsum is simply dummy text of the printing and typesetting industry. Lorem Ipsum has been the industry.</p>
  <div class="btn">LEARN MORE</div>
</div>
<div class="abs step" style="left:252px">
  <div class="icon"><svg width="26" height="14" viewBox="0 0 26 14" fill="none" stroke="#fff" stroke-width="1.5"><rect x="1" y="5" width="10" height="7" rx="3"/><rect x="15" y="5" width="10" height="7" rx="3"/><path d="M11 8h4M2 5l3-4M24 5l-3-4"/></svg></div>
  <h3>2. LENS MATERIALS</h3>
  <p>Lorem Ipsum is simply dummy text of the printing and typesetting industry. Lorem Ipsum has been the industry.</p>
  <div class="btn">LEARN MORE</div>
</div>
<div class="abs step" style="left:461px">
  <div class="icon"><svg width="26" height="26" viewBox="0 0 26 26" fill="none" stroke="#fff" stroke-width="1.5"><ellipse cx="12" cy="15" rx="8" ry="6" transform="rotate(40 12 15)"/><path d="M20 2v6M17 5h6M23 9v4M21 11h4"/></svg></div>
  <h3>3. LENS ENHANCEMENTS</h3>
  <p>Lorem Ipsum is simply dummy text of the printing and typesetting industry. Lorem Ipsum has been the industry.</p>
  <div class="btn">LEARN MORE</div>
</div>

<div class="abs labels">
  <div>VANTO</div><div>ORLEN MARK</div><div>BELLAMIRE</div><div>STRADO</div><div>MAISONE</div><div>KESTRIL</div>
</div>
<div class="abs frames">
  <div role="img" aria-label="Dark sunglasses with blue lenses"></div>
  <div role="img" aria-label="Round tortoiseshell eyeglass frames"></div>
  <div role="img" aria-label="Round sunglasses with brown gradient lenses"></div>
  <div role="img" aria-label="Thin gold metal eyeglass frames"></div>
  <div role="img" aria-label="Black cat-eye eyeglass frames"></div>
  <div role="img" aria-label="Clear frame sunglasses with brown lenses"></div>
</div>

<div class="abs footer"></div>
<div class="abs col" style="left:44px">
  <h4>Lumivue Optometry</h4>
  <div class="row"><svg width="13" height="12" viewBox="0 0 24 24" fill="#0b8db1"><path d="M5 2h4l2 6-3 2a13 13 0 0 0 6 6l2-3 6 2v4a3 3 0 0 1-3 3A19 19 0 0 1 2 5a3 3 0 0 1 3-3z"/></svg>555-210-4410</div>
  <div class="row"><svg width="13" height="12" viewBox="0 0 24 22" fill="#0b8db1"><rect x="0" y="8" width="24" height="14" rx="2"/><rect x="6" y="0" width="12" height="9"/></svg>555-210-4470</div>
  <div class="row"><svg width="13" height="10" viewBox="0 0 24 18" fill="#0b8db1"><rect width="24" height="18" rx="2"/><path d="M1 2l11 8 11-8" stroke="#f8e25c" stroke-width="2" fill="none"/></svg>care@lumivueoptics.com</div>
  <div class="row"><svg width="13" height="13" viewBox="0 0 24 24" fill="#0b8db1"><path d="M12 1a8 8 0 0 1 8 8c0 6-8 14-8 14S4 15 4 9a8 8 0 0 1 8-8z"/><circle cx="12" cy="9" r="3" fill="#f8e25c"/></svg>4820 Alderwood Ave., Fernmere,<br>CA 90412</div>
</div>
<div class="abs col" style="left:249px">
  <h4>Cedar Hollow</h4>
  <div class="row"><svg width="13" height="12" viewBox="0 0 24 24" fill="#0b8db1"><path d="M5 2h4l2 6-3 2a13 13 0 0 0 6 6l2-3 6 2v4a3 3 0 0 1-3 3A19 19 0 0 1 2 5a3 3 0 0 1 3-3z"/></svg>555-318-6020</div>
  <div class="row"><svg width="13" height="10" viewBox="0 0 24 18" fill="#0b8db1"><rect width="24" height="18" rx="2"/><path d="M1 2l11 8 11-8" stroke="#f8e25c" stroke-width="2" fill="none"/></svg>cedarhollow@lumivueoptics.com</div>
  <div class="row"><svg width="13" height="13" viewBox="0 0 24 24" fill="#0b8db1"><path d="M12 1a8 8 0 0 1 8 8c0 6-8 14-8 14S4 15 4 9a8 8 0 0 1 8-8z"/><circle cx="12" cy="9" r="3" fill="#f8e25c"/></svg>9215 Larkspur St., Suite 4,<br>Cedar Hollow, CA 90518</div>
</div>
<div class="abs col hours" style="left:456px">
  <h4>Opening Hours</h4>
  <p>Monday - Thursday : <b>9 am - 6 pm</b></p>
  <p>Friday : <b>8.30 am - 5 pm</b></p>
  <p>Saturday &nbsp;: <b>8.30 am- 5 pm</b></p>
  <p>Closed on <b>Sundays</b></p>
  <p>Please keep in mind we are closed<br>for <b>lunch 1-2 pm</b></p>
</div>

<div class="abs pill" style="left:44px">Get directions on the map<svg width="18" height="6" viewBox="0 0 18 6" fill="none" stroke="#0b8db1" stroke-width="1.2"><path d="M0 3h17M14 0l3 3-3 3"/></svg></div>
<div class="abs pill" style="left:249px">Get directions on the map<svg width="18" height="6" viewBox="0 0 18 6" fill="none" stroke="#0b8db1" stroke-width="1.2"><path d="M0 3h17M14 0l3 3-3 3"/></svg></div>
<div class="abs dot" style="left:455px;background:var(--teal)"></div>
<div class="abs dot" style="left:485px"></div>
<div class="abs dot" style="left:515px"></div>
<div class="abs dot" style="left:545px"></div>

<div class="abs copyright">Copyright © <b>LUMIVUE OPTOMETRY</b> - 2019 . All right Reserved</div>

</body>
</html>
```